Residential Remodeling Contractor needs updated business card

I need a new design for my business card.
Name of the company is Ridgefell Construction. I need a card that commands presence, strength, integrity. I have been in business for 28 years. I am a Residential Remodeling Contractor that covers all aspects of a residential remodel and build.

```html
<!DOCTYPE html>
<html lang="en">
<head>
<meta charset="utf-8">
<title>Ridgefell Construction – Business Card</title>
<link rel="stylesheet" href="https://fonts.googleapis.com/css2?family=Montserrat:wght@400;500;600;700&display=swap">
<style>
  :root {
    --navy: #233e7c;
    --white: #ffffff;
    --ink: #1e2a44;
    --backdrop: #b3b3b3;
    --soft: #d9deea;
  }
  * { box-sizing: border-box; margin: 0; padding: 0; }
  html, body {
    width: 1200px; height: 900px; overflow: hidden;
    background: var(--backdrop);
    font-family: "Montserrat", sans-serif;
  }
  .sheet {
    width: 1200px; height: 900px;
    display: flex; flex-direction: column; align-items: center; justify-content: center;
    gap: 24px;
  }
  .card {
    position: relative;
    width: 700px; height: 400px;
    background: var(--navy);
    color: var(--white);
    overflow: hidden;
  }
  /* front */
  .brand {
    position: absolute; left: 56px; top: 40px;
    font-weight: 600; text-transform: uppercase;
    letter-spacing: 2px; line-height: 1.05;
  }
  .brand .line1 { display: block; font-size: 56px; }
  .brand .line2 { display: block; font-size: 38px; margin-left: 40px; }
  .details {
    position: absolute; left: 56px; top: 196px;
    display: flex; align-items: center;
  }
  .person { text-align: right; padding-right: 22px; }
  .person-name { font-size: 26px; font-weight: 700; }
  .person-role { font-size: 13px; font-weight: 400; color: var(--soft); margin-top: 2px; }
  .divider { width: 1px; height: 78px; background: var(--soft); }
  .contacts { list-style: none; padding-left: 22px; }
  .contacts li {
    display: flex; align-items: center; gap: 12px;
    font-size: 15px; font-weight: 400; line-height: 26px;
  }
  .contacts svg { width: 16px; height: 16px; flex: none; }
  .address-band {
    position: absolute; left: 0; right: 0; top: 304px; height: 46px;
    background: var(--white); color: var(--ink);
    display: flex; align-items: center; padding-left: 56px;
    font-size: 16px; font-weight: 500;
  }
  /* back */
  .card-back { display: flex; align-items: center; justify-content: center; }
  .card-back .brand { position: static; text-align: left; }
  .card-back .brand .line1 { font-size: 50px; }
  .card-back .brand .line2 { font-size: 34px; margin-left: 36px; }
</style>
</head>
<body>
<main class="sheet">
  <section class="card card-front" aria-label="Business card front">
    <h1 class="brand"><span class="line1">Ridgefell</span><span class="line2">Construction</span></h1>
    <div class="details">
      <div class="person">
        <p class="person-name">Daniel Hart</p>
        <p class="person-role">Owner</p>
      </div>
      <span class="divider"></span>
      <ul class="contacts">
        <li>
          <svg viewBox="0 0 16 16" aria-hidden="true"><path fill="#fff" d="M3 1.5l2.5 0 1.2 3-1.6 1.2a8 8 0 0 0 5.2 5.2l1.2-1.6 3 1.2v2.5a1.5 1.5 0 0 1-1.6 1.5A13 13 0 0 1 1.5 3.1 1.5 1.5 0 0 1 3 1.5z"/></svg>
          555.014.2290
        </li>
        <li>
          <svg viewBox="0 0 16 16" aria-hidden="true"><rect x="1" y="3" width="14" height="10" rx="1" fill="#fff"/><path d="M1.5 3.5L8 9l6.5-5.5" fill="none" stroke="#233e7c" stroke-width="1.3"/></svg>
          info@ridgefellconstruction.com
        </li>
        <li>
          <svg viewBox="0 0 16 16" aria-hidden="true"><circle cx="8" cy="8" r="7" fill="#fff"/><path d="M1 8h14M8 1c-3 3.5-3 10.5 0 14M8 1c3 3.5 3 10.5 0 14" fill="none" stroke="#233e7c" stroke-width="1"/></svg>
          www.ridgefellconstruction.com
        </li>
      </ul>
    </div>
    <p class="address-band">48 Cedar Hollow Lane Brandon, MS 39047</p>
  </section>

  <section class="card card-back" aria-label="Business card back">
    <h2 class="brand"><span class="line1">Ridgefell</span><span class="line2">Construction</span></h2>
  </section>
</main>
</body>
</html>
```